Seeking funky, innovative business cards

I am looking to refresh our current business cards to something more engaging, visual and impactful. We are a management consultancy firm, see website (www.larkstone-partners.com.au). I've included our colour scheme, sample of the slides we use and our old business cards. We would like our cards to have icons. The card should display:- Name- Title- Mobile number- Address- Email address- Website - Company logo- Our purpose statement "We shape workplaces where people love to work"

Contact Information for Business Card

Brennan Ulfsson
Consultant
0468 927 341
Level 3, 218 Wexley Street, Melbourne 3000
brennan@larkstone-partners.com.au
www.larkstone-partners.com.au

Purpose statement "We shape workplaces where people love to work"
LOGO available in google images

Font styles to use
Other font styles liked:
• Open Sans Light, Bebas Neue (open to other cool foints)

Colors
ffc214
5c5c5c
f5f5f5
fefefe

Requirements
Must have
• - Name
• - Title
• - Mobile number
• - Address
• - Email address
• - Website
• - Company logo
• - Our purpose statement "We shape workplaces where people love to work"
Nice to have
• - Icons
• - Colour (see our colour scheme"

```html
<!DOCTYPE html>
<html lang="en">
<head>
<meta charset="utf-8">
<title>Larkstone Partners — Business Cards</title>
<link rel="stylesheet" href="https://fonts.googleapis.com/css2?family=Open+Sans:wght@300;400;600;700&display=swap">
<style>
  :root {
    --brand-yellow: #e3ae15;
    --brand-grey: #5c5c5c;
    --card-white: #ececec;
    --ink-dark: #3b3d3e;
    --stage: #3a3a3a;
    --on-yellow: #fefefe;
  }
  * { box-sizing: border-box; margin: 0; padding: 0; }
  html, body {
    width: 1200px; height: 829px; overflow: hidden;
    background: var(--stage);
    font-family: "Open Sans", Arial, sans-serif;
  }
  .canvas { position: relative; width: 1200px; height: 829px; }
  .card {
    position: absolute; top: 283px;
    width: 484px; height: 276px;
    background: var(--card-white);
    overflow: hidden;
  }
  .card--front { left: 82px; }
  .card--back { left: 628px; }

  .wordmark {
    position: absolute;
    display: flex; align-items: center; gap: 10px;
    color: var(--brand-grey);
    font-weight: 300;
    white-space: nowrap;
  }
  .wordmark__dot {
    flex: none; border-radius: 50%;
    background: var(--brand-yellow);
  }
  .card--front .wordmark {
    left: 0; right: 0; top: 100px; justify-content: center;
    font-size: 38px; letter-spacing: -0.5px;
  }
  .card--front .wordmark__dot { width: 13px; height: 13px; }

  .purpose-band {
    position: absolute; left: 0; right: 0; top: 229px; height: 30px;
    background: var(--brand-yellow);
    display: flex; align-items: center; justify-content: center;
    color: var(--ink-dark);
    font-size: 11.5px; font-weight: 700;
  }

  .back-shapes { position: absolute; inset: 0; }

  .card--back .wordmark {
    right: 40px; top: 70px; font-size: 19px; gap: 6px;
  }
  .card--back .wordmark__dot { width: 8px; height: 8px; }

  .contact {
    position: absolute; left: 33px; top: 113px;
    color: var(--on-yellow);
  }
  .contact__name { font-size: 15px; font-weight: 700; letter-spacing: 0.2px; line-height: 1.2; }
  .contact__title { font-size: 12px; font-weight: 400; line-height: 1.2; }
  .contact__address { margin-top: 15px; font-size: 11.5px; line-height: 14px; }
  .contact__lines { margin-top: 12px; list-style: none; font-size: 11.5px; line-height: 14.5px; }
  .contact__lines li { display: flex; align-items: center; gap: 7px; }
  .contact__icon { width: 9px; height: 9px; flex: none; }
</style>
</head>
<body>
<main class="canvas">

  <section class="card card--front">
    <div class="wordmark">
      <span class="wordmark__dot"></span>
      <span class="wordmark__name">Larkstone Partners</span>
    </div>
    <div class="purpose-band">WE SHAPE WORKPLACES WHERE PEOPLE LOVE TO WORK</div>
  </section>

  <section class="card card--back">
    <svg class="back-shapes" width="484" height="276" viewBox="0 0 484 276" aria-hidden="true">
      <polygon points="0,0 177,0 294,276 0,276" fill="var(--brand-yellow)"/>
      <polygon points="194,0 315,276 294,276" fill="var(--ink-dark)"/>
    </svg>

    <div class="wordmark">
      <span class="wordmark__dot"></span>
      <span class="wordmark__name">Larkstone Partners</span>
    </div>

    <div class="contact">
      <p class="contact__name">BRENNAN ULFSSON</p>
      <p class="contact__title">Consultant</p>
      <p class="contact__address">Level 3, 218 Wexley Street<br>Melbourne 3000</p>
      <ul class="contact__lines">
        <li>
          <svg class="contact__icon" viewBox="0 0 10 10" aria-hidden="true"><path d="M2 1 L4 3 L3 4 Q4 6 6 7 L7 6 L9 8 L8 9 Q4 9 1 5 Q1 2 2 1Z" fill="currentColor"/></svg>
          0468 927 341
        </li>
        <li>
          <svg class="contact__icon" viewBox="0 0 10 10" aria-hidden="true"><rect x="0.5" y="2" width="9" height="6" fill="none" stroke="currentColor"/><path d="M0.5 2 L5 5.5 L9.5 2" fill="none" stroke="currentColor"/></svg>
          brennan@larkstone-partners.com.au
        </li>
        <li>
          <svg class="contact__icon" viewBox="0 0 10 10" aria-hidden="true"><circle cx="5" cy="5" r="4.3" fill="none" stroke="currentColor"/><ellipse cx="5" cy="5" rx="2" ry="4.3" fill="none" stroke="currentColor"/><line x1="0.7" y1="5" x2="9.3" y2="5" stroke="currentColor"/></svg>
          www.larkstone-partners.com.au
        </li>
      </ul>
    </div>
  </section>

</main>
</body>
</html>
```